Web design for Money Service Business (uncoded)

We need a very basic website with 5-6 pages. Home page, Services, Transfer(How to use our service), About us, Contact us, FAQ
Our company name is Norvane Exchange. We are a company that deals with currency exchange and international money transfer. We do cash exchange and international money transfers to bank accounts all over the world. We offer highly competitive exchange rates so usually attract customers who transfer money over $10,000. Our niche is with larger sums of money, the design needs to be professional and communicate trust, security and stability.

```html
<!DOCTYPE html>
<html lang="en">
<head>
<meta charset="utf-8">
<title>Norvane Exchange – Services</title>
<link href="https://fonts.googleapis.com/css2?family=Arimo:ital,wght@0,400;0,700;1,400&family=Delius&display=swap" rel="stylesheet">
<style>
:root{
  --orange:#f0a030;
  --navy:#1f4f7e;
  --text:#777777;
  --heading:#3a3a3a;
  --light:#f5f5f5;
  --footer:#f2f2f2;
  --berry:#9b3a67;
  --navtext:#444444;
}
*{margin:0;padding:0;box-sizing:border-box}
html,body{width:1113px;height:1200px;overflow:hidden;background:#fff}
body{font-family:"Arimo",Arial,sans-serif;color:var(--text);position:relative}
.page{position:relative;width:1113px;height:1200px}
.abs{position:absolute}

/* header */
.site-header{left:0;top:0;width:1113px;height:100px;background:#fff}
.brand{left:73px;top:30px;display:flex;align-items:center;gap:10px}
.brand-dot{width:26px;height:26px;border-radius:50%;background:var(--navy)}
.brand-name{font-size:27px;font-weight:700;color:var(--navy);letter-spacing:-.5px}
.main-nav .item{position:absolute;top:0;height:80px;transform:translateX(-50%);text-align:center;font-size:12px;color:var(--navtext);padding-top:33px;white-space:nowrap}
.main-nav .item svg{display:block;margin:0 auto 8px;width:12px;height:12px}
.main-nav .active{background:#f4f4f4;width:88px;border-top:3px solid var(--orange);padding-top:30px}

/* title band */
.title-band{left:0;top:100px;width:1113px;height:87px;background:linear-gradient(#f0f0f0,#f6f6f6)}
.title-band .menu-icon{left:89px;top:27px}
.page-title{left:135px;top:29px;font-family:"Delius",cursive;font-size:22px;color:#333}
.page-sub{left:241px;top:36px;font-size:11px;font-style:italic;color:#888}
.page-sub:before{content:"/";font-style:normal;font-size:22px;color:#555;position:absolute;left:-17px;top:-10px}

h2.section-head{font-size:14px;font-weight:700;color:var(--heading)}
p.copy{font-size:10.6px;line-height:23px;color:var(--text)}
p.copy a{color:var(--orange);text-decoration:none}
p.copy b{color:#555}

.intro{left:90px;top:234px;width:920px}
.intro p{margin-top:10px}

/* feature boxes */
.feature{top:377px;width:223px;height:181px;background:var(--light);border-bottom:2px solid var(--orange);text-align:center;padding-top:17px}
.feature svg{display:block;margin:0 auto;height:32px}
.feature h3{font-size:12px;font-weight:700;color:var(--heading);margin-top:14px}
.feature p{font-size:10px;line-height:20px;margin:10px auto 0;width:190px}

.column{top:604px;width:440px}
.column p{margin-top:10px}

/* call to action */
.cta{left:73px;top:824px;width:967px;height:70px;background:var(--light)}
.cta-text{left:30px;top:25px;font-size:15.5px;font-style:italic;color:#666}
.cta-text span{color:var(--orange)}
.cta-button{right:30px;top:21px;width:106px;height:26px;background:var(--berry);color:#fff;font-style:italic;font-size:15px;text-align:center;line-height:26px}

/* footer */
.site-footer{left:0;top:937px;width:1113px;height:263px;background:var(--footer)}
.foot-col{top:40px}
.foot-col h4{font-size:11.5px;font-weight:700;color:var(--heading)}
.foot-about p{font-size:10px;line-height:20px;width:205px;margin-top:9px}
.foot-about a{display:block;margin-top:14px;font-size:10px;color:var(--orange);text-decoration:none}
.contact-list{list-style:none;margin-top:10px;font-size:10px}
.contact-list li{display:flex;gap:9px;line-height:21px;margin-bottom:7px}
.contact-list svg{flex:none;margin-top:6px}
.contact-list a{color:var(--orange);text-decoration:none}
.foot-rule{left:73px;top:216px;width:967px;border-top:1px dashed #d8d8d8}
.copyright{left:73px;top:231px;font-size:10px;color:#777}
.social{left:935px;top:227px;display:flex;gap:11px}
.social span{width:18px;height:18px;border-radius:50%;background:#666;display:block}
</style>
</head>
<body>
<div class="page">

<header class="site-header abs">
  <div class="brand abs"><span class="brand-dot"></span><span class="brand-name">Norvane Exchange</span></div>
  <nav class="main-nav">
    <div class="item" style="left:591px"><svg viewBox="0 0 12 12"><path d="M6 1L1 6h2v5h2.5V8h1v3H9V6h2z" fill="#888"/></svg>HOME</div>
    <div class="item" style="left:671px"><svg viewBox="0 0 12 12"><rect x="1" y="3" width="10" height="7" rx="1" fill="#888"/><rect x="4" y="2" width="4" height="2" fill="#888"/><circle cx="6" cy="6.5" r="2" fill="#fff"/></svg>TRANSFER</div>
    <div class="item active" style="left:763px"><svg viewBox="0 0 12 12"><rect x="1" y="2" width="10" height="2" fill="#888"/><rect x="1" y="5" width="10" height="2" fill="#888"/><rect x="1" y="8" width="10" height="2" fill="#888"/></svg>SERVICES</div>
    <div class="item" style="left:842px"><svg viewBox="0 0 12 12"><circle cx="6" cy="4" r="2.5" fill="#888"/><path d="M1.5 11c0-3 2-4.5 4.5-4.5s4.5 1.5 4.5 4.5z" fill="#888"/></svg>ABOUT</div>
    <div class="item" style="left:922px"><svg viewBox="0 0 12 12"><rect x="1" y="2.5" width="10" height="7" fill="#888"/><path d="M1 2.5l5 4 5-4" stroke="#fff" fill="none"/></svg>CONTACT</div>
    <div class="item" style="left:994px"><svg viewBox="0 0 12 12"><ellipse cx="5" cy="5" rx="4" ry="3" fill="#888"/><ellipse cx="8" cy="7.5" rx="3.2" ry="2.4" fill="#888"/></svg>FAQ</div>
  </nav>
</header>

<section class="title-band abs">
  <svg class="menu-icon abs" width="34" height="28" viewBox="0 0 34 28"><rect y="0" width="34" height="7" fill="#bbb"/><rect y="10" width="34" height="7" fill="#bbb"/><rect y="20" width="34" height="7" fill="#bbb"/><rect x="12" y="11.5" width="20" height="4" fill="#fff"/><rect x="12" y="21.5" width="20" height="4" fill="#fff"/></svg>
  <h1 class="page-title abs">Services</h1>
  <div class="page-sub abs">Here are the services we offer</div>
</section>

<section class="intro abs">
  <h2 class="section-head">LOREM IPSUM</h2>
  <p class="copy">Lorem ipsum dolor sit amet, consectetur adipisicing elit, sed do eiusmod tempor incididunt ut labore et. Ut wisi enim ad minim veniam, quis nostrud exerci tation ullamcorper <a href="#">suscipit lobortis</a> nisl ut aliquip ex ea commodo consequat. Lorem ipsum <b>dolor sit amet</b>, consectetur adipisicing elit, sed do eiusmod tempor incididunt ut labore et. Ut wisi enim ad minim veniam, quis nostrud exerci tation ullamcorper suscipit lobortis nisl ut aliquip ex ea commodo consequat. Lorem ipsum dolor sit amet, consectetur adipisicing elit, sed do <b>eiusmod tempor</b> incididunt.</p>
</section>

<div class="feature abs" style="left:73px">
  <svg viewBox="0 0 40 32" width="40"><path d="M2 16C8 7 14 4 20 4s12 3 18 12c-6 9-12 12-18 12S8 25 2 16z" fill="none" stroke="#555" stroke-width="3.5"/><circle cx="20" cy="16" r="7" fill="#555"/><circle cx="17.5" cy="13.5" r="2" fill="#fff"/></svg>
  <h3>COMPANY INFORMATION</h3>
  <p>Lorem ipsum dolor sit amet, consectetur adipisicing elit, sed do eiusmod tempor incididunt ut labore et.</p>
</div>
<div class="feature abs" style="left:322px">
  <svg viewBox="0 0 36 32" width="36"><rect x="2" y="2" width="32" height="28" fill="none" stroke="#555" stroke-width="3"/><rect x="2" y="2" width="32" height="6" fill="#555"/><path d="M12.5 8v22M23.5 8v22M2 15.5h32M2 23h32" stroke="#555" stroke-width="2.5"/></svg>
  <h3>NEWS SECTION</h3>
  <p>Lorem ipsum dolor sit amet, consectetur adipisicing elit, sed do eiusmod tempor incididunt ut labore et.</p>
</div>
<div class="feature abs" style="left:569px">
  <svg viewBox="0 0 38 32" width="38"><path d="M4 30L30 8" stroke="#555" stroke-width="4.5" stroke-linecap="round"/><path d="M26 11.5l4-3.5" stroke="#fff" stroke-width="2"/><path d="M9 4v6M6 7h6M20 1v4M18 3h4M33 16v5M30.5 18.5h5" stroke="#555" stroke-width="1.6"/></svg>
  <h3>DISCOUNTS SECTION</h3>
  <p>Lorem ipsum dolor sit amet, consectetur adipisicing elit, sed do eiusmod tempor incididunt ut labore et.</p>
</div>
<div class="feature abs" style="left:817px">
  <svg viewBox="0 0 36 32" width="36"><path d="M9 1h13l5 5v8H9z" fill="#555"/><rect x="1" y="15" width="34" height="11" rx="2" fill="#555"/><rect x="4" y="27" width="28" height="4" fill="#555"/><rect x="6" y="18" width="24" height="2" fill="#fff"/></svg>
  <h3>HIGH RES PRINTS</h3>
  <p>Lorem ipsum dolor sit amet, consectetur adipisicing elit, sed do eiusmod tempor incididunt ut labore et.</p>
</div>

<section class="column abs" style="left:90px">
  <h2 class="section-head">LOREM IPSUM</h2>
  <p class="copy">Lorem ipsum dolor sit amet, consectetur adipisicing elit, sed do eiusmod tempor incididunt ut labore et. Ut wisi enim ad minim veniam, quis nostrud exerci tation ullamcorper <a href="#">suscipit lobortis</a> nisl ut aliquip ex ea commodo consequat. Lorem ipsum <b>dolor sit amet</b>, consectetur adipisicing elit, sed do eiusmod tempor incididunt ut labore et. Ut wisi enim ad minim veniam, quis nostrud exerci tation ullamcorper suscipit lobortis nisl ut aliquip ex ea commodo consequat. Lorem ipsum dolor sit amet, consectetur adipisicing elit, sed do <b>eiusmod tempor</b> incididunt.</p>
</section>
<section class="column abs" style="left:585px">
  <h2 class="section-head">LOREM IPSUM</h2>
  <p class="copy">Lorem ipsum dolor sit amet, consectetur adipisicing elit, sed do eiusmod tempor incididunt ut labore et. Ut wisi enim ad minim veniam, quis nostrud exerci tation ullamcorper <a href="#">suscipit lobortis</a> nisl ut aliquip ex ea commodo consequat. Lorem ipsum <b>dolor sit amet</b>, consectetur adipisicing elit, sed do eiusmod tempor incididunt ut labore et. Ut wisi enim ad minim veniam, quis nostrud exerci tation ullamcorper suscipit lobortis nisl ut aliquip ex ea commodo consequat. Lorem ipsum dolor sit amet, consectetur adipisicing elit, sed do <b>eiusmod tempor</b> incididunt.</p>
</section>

<section class="cta abs">
  <p class="cta-text abs">Lorem ipsum <span>dolor sit amet</span>, consectetur adipisicing elit, sed do eiusmod tempor incididunt ut labore et ut wisi enim.</p>
  <a class="cta-button abs">Try It Now!</a>
</section>

<footer class="site-footer abs">
  <div class="foot-col foot-about abs" style="left:73px">
    <h4>ABOUT US</h4>
    <p>Lorem ipsum dolor sit amet, consectetur adipisicing elit, sed do eiusmod tempor incididunt ut labore et. Lorem ipsum dolor sit amet, consectetur adipisicing elit, sed do eiusmod tempor incididunt ut labore et.</p>
    <a href="#">Read more...</a>
  </div>
  <div class="foot-col abs" style="left:322px"><h4>LATEST POSTS</h4></div>
  <div class="foot-col abs" style="left:569px"><h4>PHOTO GALLERY</h4></div>
  <div class="foot-col abs" style="left:817px">
    <h4>CONTACT US</h4>
    <ul class="contact-list">
      <li><svg width="8" height="10" viewBox="0 0 8 10"><path d="M4 0a3.5 3.5 0 0 0-3.5 3.5C.5 6 4 10 4 10s3.5-4 3.5-6.5A3.5 3.5 0 0 0 4 0z" fill="#666"/><circle cx="4" cy="3.5" r="1.2" fill="#f2f2f2"/></svg><span>Address: Calle Verano 14, 20410,<br>Portmere, PM, Lunaria</span></li>
      <li><svg width="9" height="9" viewBox="0 0 9 9"><path d="M1 1l2-.5 1 2-1 1a5 5 0 0 0 2.5 2.5l1-1 2 1L8 8C4 8 1 5 1 1z" fill="#666"/></svg><span>Phone: 0041 555 01 42 908</span></li>
      <li><svg width="9" height="9" viewBox="0 0 9 9"><circle cx="4.5" cy="2.5" r="2" fill="#666"/><path d="M.5 9c0-2.5 1.8-4 4-4s4 1.5 4 4z" fill="#666"/></svg><span>Chat: Norvane_Exchange</span></li>
      <li><svg width="10" height="8" viewBox="0 0 10 8"><rect width="10" height="8" fill="#666"/><path d="M0 0l5 4 5-4" stroke="#f2f2f2" fill="none"/></svg><span>Email: <a href="#">info@norvane-exchange.com</a></span></li>
    </ul>
  </div>
  <div class="foot-rule abs"></div>
  <p class="copyright abs">Copyright 2012 Norvane Exchange - All rights reserved.</p>
  <div class="social abs"><span></span><span></span><span></span><span></span></div>
</footer>

</div>
</body>
</html>
```